Website for Ashcombe Tube Drift

Require a website for a river float in the City of Edmonton. Located on North Saskatchewan River. Will need to be a coded website with incorporated booking system through Fare Harbor software.

Pages include
Home
Pricing
About
FAQ
Contact

Ashcombe Tube Drift is an activity based business that will have customers floating down the North Saskatchewan river in Edmonton AB. The site will have all information needed and a full reservation system. The project was launched to provide people in the Edmonton area a favorite summer activity.

Here are similar websites to reference what our business will be doing and what we are looking for.

mossbankfloatco.com
quillpointpaddles.com

Target Market(s)

Families, Groups, Individuals, Anyone who wants to explore the river

Industry/Entity Type

Activities based business/ Outdoor recreational/ River Float

Coding

Coded - Design and coding required

Number of Pages Required

5+ page

Colors
0054AA
0677BA
7BADD7
CADEEF
E8F1F8
F0912C
F2A743
F7CA91
FBE8D2
FDF5EE

```html
<!DOCTYPE html>
<html lang="en">
<head>
<meta charset="utf-8">
<title>Ashcombe Tube Drift</title>
<link href="https://fonts.googleapis.com/css2?family=Montserrat:wght@400;500;600;700;800&family=Roboto:wght@400&display=swap" rel="stylesheet">
<style>
:root{
  --blue-deep:#0054AA;
  --blue:#0677BA;
  --blue-soft:#7BADD7;
  --blue-pale:#CADEEF;
  --blue-mist:#E8F1F8;
  --orange:#F0912C;
  --orange-warm:#F2A743;
  --orange-soft:#F7CA91;
  --orange-pale:#FBE8D2;
  --cream:#FDF5EE;
  --aqua:#4FC3E8;
  --grey-bg:#F2F2F2;
  --ink:#222;
  --muted:#555;
}
*{box-sizing:border-box;margin:0;padding:0}
html,body{width:1200px;height:4259px;overflow:hidden}
body{position:relative;background:#fff;font-family:'Montserrat',sans-serif;color:var(--ink)}
.abs{position:absolute}
.btn{position:absolute;display:flex;align-items:center;justify-content:center;border-radius:30px;color:#fff;font-weight:600;font-size:15px;letter-spacing:.3px}
.btn--orange{background:var(--orange);box-shadow:0 4px 10px rgba(240,145,44,.35)}
.btn--blue{background:var(--blue-deep)}

/* social text links */
.social-links{display:flex;gap:12px;font-size:12px;font-weight:600;white-space:nowrap}
.social-links span{display:flex;align-items:center;gap:5px}
.social-links span::before{content:"";width:6px;height:6px;border-radius:50%;background:currentColor}

/* header */
.topbar{left:390px;top:0;width:810px;height:60px;background:var(--orange);border-bottom-left-radius:30px;color:#fff;font-size:13px;font-weight:600;display:flex;align-items:center;gap:12px;padding-left:74px;white-space:nowrap}
.topbar .social-links{font-size:11px;gap:9px;margin-left:4px}
.brand{left:110px;top:44px;display:flex;align-items:center;gap:10px;font-weight:800;font-size:22px;color:var(--blue-deep)}
.brand__dot{width:30px;height:30px;border-radius:50%;background:var(--aqua)}
.nav{top:85px;left:530px;font-size:14px;font-weight:500;color:#333}
.nav a{position:absolute;white-space:nowrap;color:inherit;text-decoration:none}
.nav a.is-active{color:var(--orange)}

/* hero */
.hero-photo{left:0;top:140px;width:1200px;height:680px;background:linear-gradient(180deg,#8fa0b5 0%,#b7a892 35%,#6e7b5c 60%,#3f5a3b 75%,#4a6a5a 100%)}
.hero-title{top:385px;width:1200px;text-align:center;color:#fff;font-weight:700;font-size:52px;letter-spacing:.5px}
.hero-sub{top:450px;width:1200px;text-align:center;color:#fff;font-size:18px}
.hero-dots{left:574px;top:756px;display:flex;gap:10px;align-items:center}
.hero-dots span{width:9px;height:9px;border-radius:50%;background:#fff}
.hero-dots span.on{width:16px;height:16px;border:3px solid #fff;background:transparent}

/* pricing */
.pricing-bg{left:0;top:815px;width:1200px;height:792px;background:var(--grey-bg)}
.center{width:1200px;text-align:center}
.eyebrow{top:887px;color:var(--blue-deep);font-weight:700;font-size:22px}
.h-price{top:920px;font-weight:500;font-size:42px;color:#222}
.price{top:975px;color:var(--orange);font-size:44px;font-weight:500}
.price small{font-size:16px;color:#222}
.price-link{top:1040px;color:var(--blue-deep);font-size:15px;font-weight:600;text-decoration:underline}
.tagline{top:1086px;color:var(--blue-deep);font-size:21px;font-weight:500}
.subline{top:1126px;font-size:15px;color:#222}
.include{position:absolute;top:1170px;width:130px;text-align:center;font-size:15px;color:#333;line-height:1.45}
.include__tile{width:72px;height:70px;margin:0 auto 10px;background:#fff;border-radius:8px;box-shadow:0 2px 6px rgba(0,0,0,.12);display:flex;align-items:center;justify-content:center}
.include__tile svg{width:44px;height:44px;fill:none;stroke:var(--orange);stroke-width:2;stroke-linejoin:round;stroke-linecap:round}
.group{top:1390px;font-size:15px;color:#444}
.group span{color:var(--orange);text-decoration:underline}
.note{top:1423px;font-size:12px;color:#888;font-style:italic}
.slide{left:111px;top:1471px;width:978px;height:409px;background:linear-gradient(180deg,#8d8fbf 0%,#c9a9b6 40%,#7f8a7a 70%,#5d5a3e 100%)}
.arrow{width:56px;height:56px;border-radius:50%;background:#fff;box-shadow:0 2px 8px rgba(0,0,0,.2);display:flex;align-items:center;justify-content:center}

/* about */
.about-art{left:111px;top:2025px;width:443px;height:330px;border-radius:220px 220px 60px 60px;background:linear-gradient(160deg,var(--aqua),var(--blue-soft) 60%,#888)}
.bubble{position:absolute;border-radius:50%;background:var(--aqua)}
.bubble::after{content:"";position:absolute;inset:30%;border-radius:50%;background:#fff}
.about-title{left:602px;top:2008px;font-size:44px;font-weight:700;color:var(--blue-deep)}
.about-body{left:602px;top:2078px;width:490px;font-family:'Roboto',sans-serif;font-size:13px;line-height:28px;color:#555}

/* faq */
.faq-bg{left:0;top:2529px;width:726px;height:599px;background:var(--grey-bg)}
.faq-photo{left:726px;top:2529px;width:474px;height:599px;background:linear-gradient(180deg,#3f7fc6 0%,#6fa6da 45%,#a9c7e0 70%,#5a7fa0 100%)}
.faq-title{left:111px;top:2588px;font-size:36px;font-weight:700;color:var(--blue-deep)}
.faq-item{position:absolute;left:111px;width:557px;background:#fff;border:2px solid var(--blue-pale);border-radius:6px;padding:16px 20px;font-size:15px;font-weight:500;color:#222}
.faq-item .plus{position:absolute;right:18px;top:18px;width:14px;height:14px;border-radius:50%;border:2px solid var(--blue-deep)}
.faq-item .plus::before{content:"";position:absolute;left:2px;top:4px;width:6px;height:2px;background:var(--blue-deep)}
.faq-item .plus::after{content:"";position:absolute;left:4px;top:2px;width:2px;height:6px;background:var(--blue-deep)}
.faq-item p{margin-top:12px;font-size:11px;line-height:21px;color:#555;font-weight:400}
.cancel{left:367px;top:3030px;font-size:15px;color:#333;line-height:24px}
.cancel a{color:var(--blue-deep);text-decoration:underline}

/* contact */
.map{left:124px;top:3215px;width:455px;height:471px;background:linear-gradient(135deg,#e4ece0,#d7e3d2 50%,#cfdce6);box-shadow:0 4px 14px rgba(0,0,0,.15)}
.contact-title{left:643px;top:3255px;font-size:44px;font-weight:700;color:var(--blue-deep)}
.contact-sub{left:643px;top:3314px;font-size:16px;color:#333}
.contact-row{position:absolute;left:643px;display:flex;align-items:center;gap:14px}
.contact-row .icon{width:54px;height:54px;border-radius:50%;background:#fff;box-shadow:0 2px 8px rgba(0,0,0,.15);display:flex;align-items:center;justify-content:center}
.contact-row .label{color:var(--orange);font-size:16px}
.contact-row .value{font-size:18px;color:#222}

/* footer */
.footer-col{position:absolute;top:3910px;color:#fff;font-size:13.5px;font-weight:500}
.footer-col h4{font-size:13.5px;font-weight:700;margin-bottom:24px;letter-spacing:.2px}
.footer-col li{list-style:none;height:31.5px;white-space:nowrap}
.input{left:828px;top:3959px;width:258px;height:40px;border:1.5px solid #fff;border-radius:20px;color:#fff;font-size:14px;padding:10px 14px}
.copy{top:4215px;font-size:13px;color:#333}
</style>
</head>
<body>

<!-- header -->
<div class="abs topbar">
  <span>☎ Call Now - +1 555 014 2276</span><span>|</span><span>⦿ Address - 4410 87 Ave NW, Edmonton, AB</span>
  <span class="social-links" aria-label="Social links"><span>Follow</span><span>Photos</span><span>Reviews</span></span>
</div>
<div class="abs brand"><span class="brand__dot"></span>Ashcombe Tube Drift</div>
<nav class="abs nav">
  <a class="is-active" style="left:0">HOME</a>
  <a style="left:83px">PRICING</a>
  <a style="left:179px">ABOUT</a>
  <a style="left:267px">FAQ</a>
  <a style="left:334px">CONTACT</a>
  <a style="left:437px">⚲ LOGIN / SINUP</a>
</nav>
<span class="bubble" style="left:0;top:68px;width:28px;height:28px"></span>
<span class="bubble" style="left:22px;top:90px;width:48px;height:48px"></span>
<span class="bubble" style="left:1140px;top:80px;width:42px;height:42px"></span>
<span class="bubble" style="left:1172px;top:115px;width:28px;height:28px"></span>

<!-- hero -->
<div class="abs hero-photo" role="img" aria-label="Downtown Edmonton skyline above the tree-lined North Saskatchewan River"></div>
<svg class="abs" style="left:0;top:130px" width="1200" height="50" viewBox="0 0 1200 50" aria-hidden="true">
  <path d="M0 0H1200V10C1150 40 1100 40 1050 20S950 0 900 25 800 45 750 22 650 0 600 25 500 45 450 22 350 0 300 25 200 45 150 22 50 0 0 25Z" fill="#fff"/>
</svg>
<svg class="abs" style="left:0;top:740px" width="1200" height="90" viewBox="0 0 1200 90" aria-hidden="true">
  <path d="M0 30C300 85 900 85 1200 20V90H0Z" fill="var(--grey-bg)"/>
  <path d="M0 30C300 85 900 85 1200 20" fill="none" stroke="var(--blue-deep)" stroke-width="7"/>
</svg>
<h1 class="abs hero-title">ASHCOMBE TUBE DRIFT</h1>
<p class="abs hero-sub">Float the North Saskatchewan through downtown Edmonton</p>
<div class="btn btn--orange" style="left:483px;top:491px;width:228px;height:48px">BOOK NOW</div>
<div class="abs hero-dots"><span></span><span class="on"></span><span></span></div>

<!-- pricing -->
<div class="abs pricing-bg"></div>
<p class="abs center eyebrow">PRICING</p>
<h2 class="abs center h-price">Tube and Shuttle</h2>
<p class="abs center price">$30<small>/person</small></p>
<p class="abs center price-link">BOOK NOW ✔</p>
<p class="abs center tagline">We keep our pricing simple and include everything you need</p>
<p class="abs center subline">Premium comfort float tube with backrest and cup holder</p>

<div class="include" style="left:171px"><div class="include__tile"><svg viewBox="0 0 44 44" role="img" aria-label="Lifejacket icon"><path d="M14 6h5l3 5 3-5h5l6 8v24H8V14Z"/><path d="M22 11v27M8 22h28M8 30h28"/></svg></div>Lifejacket</div>
<div class="include" style="left:289px"><div class="include__tile"><svg viewBox="0 0 44 44" role="img" aria-label="Paddle icon"><ellipse cx="17" cy="13" rx="5" ry="9"/><path d="M17 22v18"/><ellipse cx="29" cy="31" rx="5" ry="9"/><path d="M29 22V4"/></svg></div>Paddle</div>
<div class="include" style="left:413px"><div class="include__tile"><svg viewBox="0 0 44 44" role="img" aria-label="Shuttle bus icon"><rect x="8" y="6" width="28" height="28" rx="4"/><path d="M8 20h28M12 10h20v10H12Z"/><circle cx="14" cy="27" r="2"/><circle cx="30" cy="27" r="2"/><path d="M12 34v4M32 34v4"/></svg></div>Round trip<br>shuttle service</div>
<div class="include" style="left:545px"><div class="include__tile"><svg viewBox="0 0 44 44" role="img" aria-label="Safety training icon"><path d="M22 5 36 10v11c0 9-6 15-14 18C14 36 8 30 8 21V10Z"/><path d="m15 21 5 5 9-10"/></svg></div>Safety<br>training</div>
<div class="include" style="left:654px;top:1167px"><div class="include__tile"><svg viewBox="0 0 44 44" role="img" aria-label="Staff assistance icon"><path d="M10 24v-4a12 12 0 0 1 24 0v4"/><rect x="7" y="22" width="6" height="10" rx="2"/><rect x="31" y="22" width="6" height="10" rx="2"/><path d="M34 32c0 5-5 7-10 7"/></svg></div>Staff<br>assistance</div>
<div class="include" style="left:773px;top:1167px"><div class="include__tile"><svg viewBox="0 0 44 44" role="img" aria-label="Parking icon"><rect x="7" y="7" width="30" height="30" rx="4"/><path d="M17 31V14h7a5 5 0 0 1 0 10h-7"/></svg></div>Parking</div>
<div class="include" style="left:897px;top:1167px"><div class="include__tile"><svg viewBox="0 0 44 44" role="img" aria-label="Fun icon"><path d="m22 6 4 10 10 1-8 7 3 10-9-6-9 6 3-10-8-7 10-1Z"/><path d="M36 32l2 2M8 32l-2 2"/></svg></div>Unlimited<br>Fun!</div>

<div class="btn btn--blue" style="left:486px;top:1322px;width:228px;height:52px">BOOK NOW</div>
<p class="abs center group">Group of 10 or more? <span>Contact us</span></p>
<p class="abs center note">*does not include taxes or fees</p>

<div class="abs slide" role="img" aria-label="Arched white bridge over the river at sunset with the downtown skyline behind"></div>
<div class="abs arrow" style="left:84px;top:1647px"><svg width="14" height="14" viewBox="0 0 14 14"><path d="M9 2 4 7l5 5" fill="none" stroke="var(--blue-deep)" stroke-width="2"/></svg></div>
<div class="abs arrow" style="left:1058px;top:1647px"><svg width="14" height="14" viewBox="0 0 14 14"><path d="m5 2 5 5-5 5" fill="none" stroke="var(--blue-deep)" stroke-width="2"/></svg></div>

<!-- about -->
<div class="abs about-art" role="img" aria-label="Illustration of a river tube beneath an arched bridge"></div>
<span class="bubble" style="left:480px;top:1986px;width:40px;height:40px"></span>
<span class="bubble" style="left:510px;top:2025px;width:66px;height:66px"></span>
<span class="bubble" style="left:72px;top:2370px;width:62px;height:62px"></span>
<span class="bubble" style="left:124px;top:2420px;width:42px;height:42px"></span>
<h2 class="abs about-title">About Us</h2>
<p class="abs about-body">Float the North Saskatchewan through downtown Edmonton Edmonton's Best Summer Activity We provide the lifejacket, paddle, river tube and shuttle service. You just have to show up. Ashcombe Tube Drift was launched to provide people in the Edmonton area a favorite summer activity. Nothing is better on a hot summer day, than spending it on the river and seeing Edmonton from a new perspective. Our home base and meeting spot is at Cedar Landing (Map Link), by the Larkspur Conservatory. This is where you will check in, and board the shuttle.</p>
<div class="btn btn--orange" style="left:600px;top:2331px;width:227px;height:50px">BOOK NOW</div>

<!-- faq -->
<div class="abs faq-bg"></div>
<div class="abs faq-photo" role="img" aria-label="Kids in lifejackets jumping from a boat into the lake"></div>
<h2 class="abs faq-title">Frequently Asked Questions</h2>
<div class="faq-item" style="top:2656px;height:57px">How do I reserve my float?<span class="plus"></span></div>
<div class="faq-item" style="top:2725px;height:57px">What safety information should I know?<span class="plus"></span></div>
<div class="faq-item" style="top:2795px;height:126px">What is included?<span class="plus"></span>
  <p>We provide round trip shuttle service and everything you need to have a fun and safe time on the river. All floaters will receive round trip shuttle service, a premium tube complete with backrest and cup holder, lifejacket, paddle, safety demonstration and fun.</p></div>
<div class="faq-item" style="top:2934px;height:57px">What should I bring?<span class="plus"></span></div>
<div class="btn btn--orange" style="left:112px;top:3028px;width:228px;height:50px">VIEW MORE</div>
<p class="abs cancel">To cancel, please email<br><a>info@ashcombetubedrift.com</a> or call us.</p>

<!-- contact -->
<div class="abs map" role="img" aria-label="Street map of Edmonton showing the river and the launch location"></div>
<h2 class="abs contact-title">Contact Us</h2>
<p class="abs contact-sub">We'd love to hear from you!</p>
<div class="contact-row" style="top:3365px"><span class="icon"><svg width="16" height="16" viewBox="0 0 16 16"><path d="M3 1l3 3-2 2c1 2 3 4 5 5l2-2 3 3-2 3C7 15 1 9 1 3Z" fill="var(--blue-deep)"/></svg></span><div><div class="label">Call Now</div><div class="value">+1 555 014 2276</div></div></div>
<div class="contact-row" style="top:3449px"><span class="icon"><svg width="16" height="12" viewBox="0 0 16 12"><rect width="16" height="12" rx="1" fill="var(--blue-deep)"/><path d="M0 1l8 6 8-6" fill="none" stroke="#fff" stroke-width="1.4"/></svg></span><div><div class="label">Email</div><div class="value">info@ashcombetubedrift.com</div></div></div>
<div class="contact-row" style="top:3535px"><span class="icon"><svg width="12" height="16" viewBox="0 0 12 16"><path d="M6 0a6 6 0 0 1 6 6c0 4-6 10-6 10S0 10 0 6a6 6 0 0 1 6-6Z" fill="var(--blue-deep)"/><circle cx="6" cy="6" r="2" fill="#fff"/></svg></span><div><div class="label">Address</div><div class="value">4410 87 Ave NW, Edmonton</div></div></div>
<div class="abs social-links" style="left:660px;top:3616px;color:#333;font-size:13px" aria-label="Social links"><span>Follow</span><span>Photos</span><span>Reviews</span></div>

<!-- footer -->
<svg class="abs" style="left:0;top:3770px" width="1200" height="489" viewBox="0 0 1200 489" aria-hidden="true">
  <path d="M0 20C300 -10 900 -10 1200 40V60C900 10 300 10 0 40Z" fill="var(--orange)"/>
  <path d="M0 40C300 10 900 10 1200 60V410C1150 440 1100 440 1050 420S950 400 900 425 800 445 750 422 650 400 600 425 500 445 450 422 350 400 300 425 200 445 150 422 50 400 0 425Z" fill="var(--blue-deep)"/>
</svg>
<span class="bubble" style="left:12px;top:4040px;width:34px;height:34px"></span>
<span class="bubble" style="left:36px;top:4066px;width:50px;height:50px"></span>
<span class="bubble" style="left:1116px;top:4045px;width:44px;height:44px"></span>
<span class="bubble" style="left:1154px;top:4082px;width:28px;height:28px"></span>

<div class="footer-col" style="left:111px">
  <h4>ASHCOMBE TUBE DRIFT CONNECT</h4>
  <ul><li>✉ EMAIL: info@ashcombetubedrift.com</li><li>⦿ LOCATION: Cedar Landing</li>
  <li><span class="social-links" aria-label="Social links"><span>Follow</span><span>Photos</span><span>Reviews</span></span></li></ul>
</div>
<div class="footer-col" style="left:430px">
  <h4>FLOATING 7 DAYS A WEEK</h4>
  <ul><li>◷ Hours</li><li>Mon - Fri 9:00am - 5:00pm</li><li>Sat - 10:00am - 5:00pm</li><li>Sunday - 9:30am - 5:00am</li></ul>
</div>
<div class="footer-col" style="left:676px">
  <h4>NAVIGATION</h4>
  <ul><li>Home</li><li>Pricing</li><li>About</li><li>Faq</li><li>Contact</li></ul>
</div>
<div class="footer-col" style="left:830px"><h4>SIGN UP FOR OUR MAILING LIST</h4></div>
<div class="abs input">Enter Email</div>
<div class="btn btn--orange" style="left:828px;top:4010px;width:180px;height:40px;font-size:14px">SUBSCRIBE</div>

<p class="abs center copy">© 2022 All Rights Reserved</p>
</body>
</html>
```